Business Card Design Project

Business card based on attached logo

Todd Merrick
Todd@lorvantest.com
877-514-9073 ext. 318
Www.LorvanTest.com

Industry/Entity Type

Business

```html
<!DOCTYPE html>
<html lang="en">
<head>
<meta charset="utf-8">
<title>LorvanTest Business Cards</title>
<link rel="stylesheet" href="https://fonts.googleapis.com/css2?family=Questrial&display=swap">
<style>
  :root {
    --brand-red: #ea1c24;
    --brand-ink: #231f20;
    --paper: #ffffff;
    --paper-light: #f4f4f5;
    --paper-shade: #dfe0e2;
    --table: #7b3b1f;
    --text-font: "Questrial", "Century Gothic", sans-serif;
  }
  * { box-sizing: border-box; margin: 0; padding: 0; }
  html, body {
    width: 1200px;
    height: 736px;
    overflow: hidden;
  }
  body {
    position: relative;
    background: var(--table);
    font-family: var(--text-font);
  }
  .card {
    position: absolute;
    width: 503px;
    height: 287px;
    overflow: hidden;
    box-shadow: 0 2px 6px rgba(0,0,0,0.35);
  }
  .card--contact { left: 65px; top: 64px;
    background: radial-gradient(ellipse at 40% 35%, var(--paper-light) 0%, var(--paper-shade) 100%); }
  .card--white { left: 614px; top: 67px; background: var(--paper); }
  .card--red   { left: 80px;  top: 391px; background: var(--brand-red); }
  .card--black { left: 613px; top: 391px; background: var(--brand-ink); }

  /* wordmark */
  .wordmark {
    display: flex;
    align-items: center;
    gap: 10px;
    font-family: var(--text-font);
    font-weight: 400;
    letter-spacing: 0.01em;
    line-height: 1;
    white-space: nowrap;
  }
  .wordmark__square {
    display: block;
    background: var(--brand-red);
    flex: none;
  }

  /* contact card */
  .card--contact .wordmark {
    position: absolute;
    left: 36px; top: 104px;
    font-size: 36px;
    color: var(--brand-ink);
  }
  .card--contact .wordmark__square { width: 18px; height: 18px; }
  .divider {
    position: absolute;
    left: 253px; top: 50px;
    width: 1px; height: 136px;
    background: #b9babd;
  }
  .contact {
    position: absolute;
    left: 274px; top: 58px;
    list-style: none;
  }
  .contact__name {
    font-size: 21px;
    color: var(--brand-red);
    letter-spacing: 0.04em;
    margin-bottom: 16px;
    font-weight: 400;
    -webkit-text-stroke: 0.4px var(--brand-red);
  }
  .contact__item {
    display: flex;
    align-items: center;
    gap: 7px;
    font-size: 13.5px;
    color: var(--brand-ink);
    height: 24px;
  }
  .contact__icon { width: 10px; height: 10px; flex: none; }
  .band {
    position: absolute;
    left: 0; bottom: 0;
    width: 100%; height: 44px;
    display: flex;
  }
  .band__dark { width: 214px; background: var(--brand-ink); }
  .band__red  { flex: 1; background: var(--brand-red); }
  .band__disc {
    position: absolute;
    left: 214px; top: 213px;
    width: 74px; height: 74px;
    border-radius: 50%;
    background: radial-gradient(circle at 45% 40%, #f7f7f8 0%, #dcdde0 100%);
  }

  /* front cards */
  .front {
    position: absolute;
    inset: 0;
    display: flex;
    flex-direction: column;
    align-items: center;
  }
  .front .wordmark {
    margin-top: 74px;
    font-size: 64px;
  }
  .front .wordmark__square { width: 30px; height: 30px; }
  .front__tagline {
    margin-top: 56px;
    font-size: 16px;
    letter-spacing: 0.11em;
  }
  .front__url {
    margin-top: 18px;
    font-size: 16px;
    letter-spacing: 0.14em;
  }
  .card--white .wordmark { color: var(--brand-ink); }
  .card--white .front__tagline { color: var(--brand-red); }
  .card--white .front__url { color: var(--brand-ink); }

  .card--red .wordmark,
  .card--red .front__tagline,
  .card--red .front__url { color: var(--paper); }
  .card--red .wordmark__square { background: var(--paper); }

  .card--black .wordmark,
  .card--black .front__tagline,
  .card--black .front__url { color: var(--paper); }
</style>
</head>
<body>

  <section class="card card--contact" aria-label="Business card, contact side">
    <div class="wordmark"><span>LorvanTest</span><span class="wordmark__square"></span></div>
    <div class="divider"></div>
    <ul class="contact">
      <li class="contact__name">Todd Merrick</li>
      <li class="contact__item">
        <svg class="contact__icon" viewBox="0 0 10 10" aria-hidden="true">
          <circle cx="5" cy="5" r="4.3" fill="none" stroke="#ea1c24" stroke-width="1.2"/>
          <path d="M3.4 2.8 L4.4 3.9 L3.9 4.5 Q4.6 5.8 5.6 6.2 L6.2 5.7 L7.2 6.7 L6.5 7.4 Q4.3 7 2.8 3.6 Z" fill="#ea1c24"/>
        </svg>
        877-514-9073 ext. 318
      </li>
      <li class="contact__item">
        <svg class="contact__icon" viewBox="0 0 10 10" aria-hidden="true">
          <rect x="0.5" y="2" width="9" height="6.5" fill="#ea1c24"/>
          <path d="M0.5 2 L5 5.6 L9.5 2" fill="none" stroke="#fff" stroke-width="0.9"/>
        </svg>
        Todd@lorvantest.com
      </li>
      <li class="contact__item">
        <svg class="contact__icon" viewBox="0 0 10 10" aria-hidden="true">
          <g fill="none" stroke="#ea1c24" stroke-width="0.9">
            <circle cx="5" cy="5" r="4.3"/>
            <ellipse cx="5" cy="5" rx="1.9" ry="4.3"/>
            <path d="M0.7 5 H9.3 M1.4 2.8 H8.6 M1.4 7.2 H8.6"/>
          </g>
        </svg>
        www.LorvanTest.com
      </li>
    </ul>
    <div class="band"><span class="band__dark"></span><span class="band__red"></span></div>
    <div class="band__disc"></div>
  </section>

  <section class="card card--white" aria-label="Business card, white front">
    <div class="front">
      <div class="wordmark"><span>LorvanTest</span><span class="wordmark__square"></span></div>
      <p class="front__tagline">Expert Online HIPAA Training</p>
      <p class="front__url">www.LorvanTest.com</p>
    </div>
  </section>

  <section class="card card--red" aria-label="Business card, red front">
    <div class="front">
      <div class="wordmark"><span>LorvanTest</span><span class="wordmark__square"></span></div>
      <p class="front__tagline">Expert Online HIPAA Training</p>
      <p class="front__url">www.LorvanTest.com</p>
    </div>
  </section>

  <section class="card card--black" aria-label="Business card, black front">
    <div class="front">
      <div class="wordmark"><span>LorvanTest</span><span class="wordmark__square"></span></div>
      <p class="front__tagline">Expert Online HIPAA Training</p>
      <p class="front__url">www.LorvanTest.com</p>
    </div>
  </section>

</body>
</html>
```